Flat bootstrap design for existing site

I'm looking for a modern flat design based around an existing logo. This has to be a custom design (no external templates), and implemented into a bootstrap framework.

The logo is attached as 2 versions - choose whichever you want, that flows better with whatever design you choose.

Added screenshots of the existing site (currently using the default bootstrap layouts). Please make your designs around those pages in the screenshots (i.e. the homepage only has the postal code input and the header). The active page has 3 screenshots, because I wanted to illustrate the other states that would be visible (in the table rows).

This is a moving/junk removal website, just for some context.

Here's some example websites (flat designs) that I like, just to give you an idea of what I'm after.

https://www.plimvora.com/
https://dacklow.com/
https://trevanu.com/
https://quobrintal.com/en/

Coding

Coded - Design and coding required

Number of Pages Required

5+ page

Colors

Designer to choose colors to be used in the design.

Requirements
Must have
• It must be a modern/simple flat design, that is built around the existing logo (attached).
• It has to be implemented using bootstrap.

```html
<!DOCTYPE html>
<html lang="en">
<head>
<meta charset="utf-8">
<title>Haulvex – Booking Details</title>
<link href="https://fonts.googleapis.com/css2?family=Roboto:wght@400;500&display=swap" rel="stylesheet">
<style>
  :root{
    --brand:#4bc9f4;
    --brand-dark:#3bb7e0;
    --alert:#8fdcf6;
    --page:#f7f7f7;
    --white:#ffffff;
    --border:#dedede;
    --text:#5e5e5e;
    --muted:#7a7a7a;
    --table-head:#8a8a8a;
    --accepted:#71b562;
    --pending:#676767;
    --footer:#5b5b5b;
  }
  *{box-sizing:border-box;margin:0;padding:0}
  html,body{width:1200px;height:1089px;overflow:hidden}
  body{background:var(--page);font-family:"Roboto",Arial,sans-serif;color:var(--text);position:relative}

  .site-header{position:absolute;left:0;top:0;width:1200px;height:88px;background:var(--brand)}
  .brand{position:absolute;left:86px;top:22px;display:flex;align-items:center;gap:10px;color:var(--white);font-size:34px;font-weight:500;letter-spacing:1px}
  .brand-dot{width:34px;height:34px;border-radius:50%;background:var(--white)}
  .main-nav a{position:absolute;top:0;height:88px;line-height:88px;color:var(--white);font-size:13px;font-weight:500;text-decoration:none;text-transform:uppercase}
  .nav-book{left:545px}
  .nav-how{left:636px}
  .nav-driver{left:757px;width:161px;text-align:center;background:var(--brand-dark)}
  .nav-account{left:950px;text-transform:none !important;font-size:13px}
  .caret{position:absolute;left:1099px;top:41px}

  .card{position:absolute;left:86px;top:150px;width:1028px;height:343px;background:var(--white);border:1px solid var(--border);border-radius:3px}
  .card-title{height:63px;line-height:63px;padding-left:17px;font-size:16px;font-weight:500;color:var(--text);border-bottom:1px solid #eeeeee}
  .label{position:absolute;font-size:14px;font-weight:500;color:var(--muted)}
  .field{position:absolute;height:41px;border:1px solid var(--border);border-radius:3px;background:var(--white);font-size:12.5px;color:var(--text);padding:0 13px;line-height:39px}
  .addon{position:absolute;top:0;right:0;width:39px;height:39px;border-left:1px solid var(--border);background:#f9f9f9;display:flex;align-items:center;justify-content:center}
  .textarea{line-height:normal;padding-top:12px}
  .btn-update{position:absolute;left:16px;top:279px;width:106px;height:39px;background:var(--brand);color:var(--white);font-size:14px;font-weight:500;border:none;border-radius:2px;text-align:center;line-height:39px}

  .section-title{position:absolute;left:86px;top:533px;font-size:16px;font-weight:500;color:var(--text)}
  .notice{position:absolute;left:86px;top:567px;width:1028px;height:53px;background:var(--alert);border-radius:3px;color:var(--white);font-size:12.5px;font-weight:500;line-height:53px;padding-left:22px}

  .drivers{position:absolute;left:86px;top:655px;width:1028px;border-collapse:collapse;background:var(--white);border:1px solid var(--border)}
  .drivers th,.drivers td{width:205.6px;border-right:1px solid var(--border);text-align:left}
  .drivers th:last-child,.drivers td:last-child{border-right:none}
  .drivers th{height:53px;background:var(--table-head);color:var(--white);font-size:12.5px;font-weight:500;padding-left:25px}
  .drivers td{height:63px;border-top:1px solid #e6e6e6;font-size:14px;color:var(--muted);padding-left:27px}
  .drivers td.status{padding-left:35px}
  .badge{display:inline-block;width:128px;height:33px;line-height:33px;text-align:center;color:var(--white);font-size:11.5px;font-weight:500;text-transform:uppercase}
  .badge-accepted{background:var(--accepted)}
  .badge-sent{background:var(--brand)}
  .badge-pending{background:var(--pending)}
  .drivers td.note{padding-left:31px}

  .site-footer{position:absolute;left:0;top:1020px;width:1200px;height:69px;background:var(--footer)}
  .copyright{position:absolute;left:86px;top:27px;color:var(--white);font-size:12px;font-weight:500}
  .social{position:absolute;left:942px;top:19px;display:flex;gap:5px}
  .social span{width:30px;height:30px;border:1.5px solid var(--white);border-radius:50%}
</style>
</head>
<body>
  <header class="site-header">
    <div class="brand"><span class="brand-dot"></span>HAULVEX</div>
    <nav class="main-nav">
      <a class="nav-book" href="#">Book</a>
      <a class="nav-how" href="#">How it works</a>
      <a class="nav-driver" href="#">Become a driver</a>
      <a class="nav-account" href="#">dana@brellmoor.com</a>
    </nav>
    <svg class="caret" width="9" height="6" viewBox="0 0 9 6"><path d="M0 0h9L4.5 6z" fill="#fff"/></svg>
  </header>

  <section class="card">
    <h2 class="card-title">BOOKING DETAILS</h2>
    <span class="label" style="left:18px;top:78px">Package Selected :</span>
    <span class="label" style="left:531px;top:78px">Pick-up time selected :</span>
    <div class="field" style="left:16px;top:105px;width:484px">Package 1
      <span class="addon"><svg width="8" height="11" viewBox="0 0 8 11"><path d="M4 0l4 4.5H0zM4 11L0 6.5h8z" fill="#666"/></svg></span>
    </div>
    <div class="field" style="left:529px;top:105px;width:484px">July 18 at 0:13 am
      <span class="addon"><svg width="12" height="12" viewBox="0 0 12 12"><rect x="0.5" y="1.5" width="11" height="10" fill="none" stroke="#666"/><rect x="0.5" y="1.5" width="11" height="2.5" fill="#666"/><path d="M2 6h8M2 8h8M2 10h8M4 4v7M6 4v7M8 4v7" stroke="#666" stroke-width=".6"/></svg></span>
    </div>
    <span class="label" style="left:18px;top:172px">Description :</span>
    <div class="field textarea" style="left:16px;top:199px;width:992px;height:62px">1 Large Stove</div>
    <div class="btn-update">UPDATE</div>
  </section>

  <h2 class="section-title">DRIVERS IN YOUR AREA</h2>
  <div class="notice">Please stey on this page and be patient,while we contact the drivers and find your one ASAP.</div>

  <table class="drivers">
    <thead>
      <tr><th>NAME</th><th>DISTANCE (KM)</th><th>AGREED PICK-UP TIME</th><th></th><th></th></tr>
    </thead>
    <tbody>
      <tr><td>Corbin Hale</td><td>4.04km away</td><td>July 18at 4.13am</td><td class="status"><span class="badge badge-accepted">Time accepted</span></td><td class="note">Payment made</td></tr>
      <tr><td>Miles Dunmore</td><td>5.7km away</td><td>-</td><td class="status"><span class="badge badge-sent">Request sent</span></td><td></td></tr>
      <tr><td>Edgar Wollis</td><td>11.13km away</td><td>-</td><td class="status"><span class="badge badge-sent">Request sent</span></td><td></td></tr>
      <tr><td>Ravi Keaton</td><td>11.91km away</td><td>-</td><td class="status"><span class="badge badge-pending">Pending</span></td><td></td></tr>
    </tbody>
  </table>

  <footer class="site-footer">
    <p class="copyright">© Copyright 2017 Haulvex.All Rights Reserved.</p>
    <div class="social" aria-label="Social links"><span></span><span></span><span></span><span></span><span></span></div>
  </footer>
</body>
</html>
```